Golden Coat All-Purpose Breading Bag Design

Our client, Halvern Food Products, is looking to re-design the packaging for their product, Pellham's Golden Coat. Goldn Coat is an all-purpose food breading mix.

Halvern Foods has a registered trademark for this product, but they have not been using it for this particular 10 pound bag. They want to get the trademark onto the bag and also give the bag an updated look. They would like to continue to use the same red and blue colors. This 10 pound bag is not available on store shelves; it is sold to food service distributors who sell to restaurants.

All of the copy on the existing bag is still relevant, so we will want to incoprporate it into the bag design. Once these bags are filled with product, the tops get folded over about 1 inch and then sewn shut with thread.

Eventually, we will need the design applied to the Bag Template file attached, but that isn't important until a design is selected.

Target Market(s)

Restaurants

Industry/Entity Type

Food Manufacturing

Colors
0054AA
0677BA
7BADD7
CADEEF
E8F1F8
EB3D1F
EC4F4E
F09395
F8D3D4
FCEDEE

Requirements
Must have
• Trademark introduced to the design

```html
<!DOCTYPE html>
<html lang="en">
<head>
<meta charset="utf-8">
<title>Pellham's Golden Coat – 10 lb Bag Front</title>
<link href="https://fonts.googleapis.com/css2?family=Montserrat:wght@700;800&family=Barlow+Condensed:ital,wght@1,700&display=swap" rel="stylesheet">
<style>
  :root {
    --red: #cf2129;
    --navy: #1f3a85;
    --white: #ffffff;
    --paper: #ffffff;
    --crumb-light: #e7a75a;
    --crumb-mid: #c9772e;
    --crumb-dark: #8f4a1c;
    --table: #eadbc9;
  }
  * { margin: 0; padding: 0; box-sizing: border-box; }
  html, body { width: 1200px; height: 953px; overflow: hidden; background: var(--paper); }
  .canvas { position: relative; width: 1200px; height: 953px; background: var(--paper); }
  .bag-front { position: absolute; left: 316px; top: 53px; width: 568px; height: 847px; }

  .tagline {
    position: absolute; left: 0; top: 10px; width: 568px; text-align: center;
    font-family: "Barlow Condensed", sans-serif; font-style: italic; font-weight: 700;
    font-size: 22px; line-height: 24px; color: var(--navy); letter-spacing: .5px;
    transform: rotate(-4deg);
  }
  .tagline .accent { color: var(--red); border-bottom: 2px solid var(--red); }

  .hero-panel { position: absolute; left: 0; top: 125px; width: 568px; height: 359px; background: var(--red); }

  .brand-name {
    position: absolute; left: 0; top: 88px; width: 568px; text-align: center;
    font-family: "Montserrat", sans-serif; font-weight: 800; font-size: 30px; color: var(--navy);
  }

  .product-name {
    position: absolute; font-family: "Montserrat", sans-serif; font-weight: 800; color: var(--white);
    line-height: 1;
  }
  .product-name.line-one { left: 52px; top: 175px; font-size: 104px; letter-spacing: -3px; }
  .product-name.line-two { left: 262px; top: 296px; font-size: 104px; letter-spacing: -3px; }

  .descriptor {
    position: absolute; left: 112px; top: 336px; width: 150px; text-align: center;
    font-family: "Montserrat", sans-serif; font-weight: 800; font-size: 21px; line-height: 23px;
    color: var(--white); letter-spacing: 1px;
  }

  .food-photo {
    position: absolute; left: 0; top: 484px; width: 568px; height: 277px;
    background: radial-gradient(ellipse at 45% 55%, var(--crumb-light) 0%, var(--crumb-mid) 45%, var(--crumb-dark) 75%, var(--table) 100%);
  }

  .claim-box {
    position: absolute; left: 105px; top: 444px; width: 360px; height: 88px;
    background: var(--navy); color: var(--white); text-align: center; padding-top: 12px;
  }
  .claim-box .claim {
    font-family: "Montserrat", sans-serif; font-weight: 700; font-size: 18px; letter-spacing: 2px;
  }
  .claim-box .claim-detail {
    font-family: "Barlow Condensed", sans-serif; font-style: italic; font-weight: 700;
    font-size: 15px; line-height: 19px; margin-top: 4px; letter-spacing: .5px;
  }

  .ingredients {
    position: absolute; left: 0; top: 770px; width: 568px; text-align: center;
    font-family: "Montserrat", sans-serif; font-weight: 700; font-size: 12px; line-height: 18px; color: var(--navy);
  }
  .net-weight {
    position: absolute; left: 0; top: 815px; width: 568px; text-align: center;
    font-family: "Montserrat", sans-serif; font-weight: 800; font-size: 20px; letter-spacing: 2px; color: var(--navy);
  }
</style>
</head>
<body>
<div class="canvas">
  <div class="bag-front">
    <p class="tagline">CHICKEN FRIED THE GOLDEN COAT WAY<br>IS FRIED CHICKEN <span class="accent">THE RIGHT WAY.</span></p>

    <div class="hero-panel"></div>
    <div class="food-photo" role="img" aria-label="Photo of crispy golden fried chicken pieces on parchment"></div>

    <div class="brand-name">Pellham's</div>
    <div class="product-name line-one">Golden</div>
    <div class="product-name line-two">Coat</div>
    <p class="descriptor">THE ALL PURPOSE BREADING</p>

    <div class="claim-box">
      <p class="claim">SEALS JUICE IN- GREASE OUT</p>
      <p class="claim-detail">COOKS TWO-POUND CHICKEN WELL DONE<br>IN 10 MINUTES (DEEP FAT).</p>
    </div>

    <p class="ingredients">INGREDIENTS: FLOUR, SALT, NON-FAT MILK SOLIDS, EGG YOLK,<br>BAKING POWDER, CORN STARCH, SUGAR AND PEPPER.</p>
    <p class="net-weight">NET WT. 10 LBS.</p>
  </div>
</div>
</body>
</html>
```